Custom Software Solutions

web design for a small custom programming company in Brisbane Australia. Specialize in business finance solutions, DeskSuite automation and programming and data analysis. The design should portray professionalism and honesty. Main applications deal with financial accounting reporting and analysis. Would like to see colors blue and purple used (but sparsely). added file is company logo. Trading name is TR Solutions, while the official company name is TR Solutions (QLD) Pty Ltd.

Target Market(s)

current clients for support
marketing tool for prospective clients

Industry/Entity Type

Business

Number of Pages Required

5+ page

Font styles to use
Sans Serif

Colors
0555a3
a54599
ffffff

Requirements
Must have
• introduction
• blog for news and tips
• previous and current clients/projects page
• contact us page with email submission form
Should not have
• social media links

```html
<!DOCTYPE html>
<html lang="en">
<head>
<meta charset="utf-8">
<title>TR Solutions</title>
<link href="https://fonts.googleapis.com/css2?family=Open+Sans:ital,wght@0,400;0,600;1,400&family=Arimo:wght@400&display=swap" rel="stylesheet">
<style>
:root{
  --brand:#134a84;
  --ink:#333;
  --muted:#555;
  --line:#dcdcdc;
  --band:#f5f5f5;
  --footer:#2b2b2b;
  --icon:#6b6b6b;
}
*{margin:0;padding:0;box-sizing:border-box}
html,body{width:873px;height:1200px;overflow:hidden;background:#fff}
body{position:relative;font-family:'Arimo',Arial,sans-serif;color:var(--ink)}
a{text-decoration:none}
.abs{position:absolute}

.site-header{left:0;top:0;width:873px;height:56px;border-bottom:1px solid var(--line);background:#fff}
.brand{left:131px;top:14px;display:flex;align-items:center;gap:7px}
.brand-dot{width:18px;height:18px;border-radius:50%;background:var(--brand)}
.brand-name{font-family:'Open Sans',sans-serif;font-size:15px;color:var(--brand);letter-spacing:1px}
.nav a{position:absolute;top:18px;height:20px;line-height:20px;font-size:10px;color:#555}
.nav .active{left:374px;width:61px;background:var(--brand);color:#fff;text-align:center}

.hero{left:0;top:56px;width:873px;height:284px;background:linear-gradient(100deg,#8f98a4 0%,#c6ccd4 30%,#3a4a66 55%,#d7dde4 80%,#efe6dd 100%)}
.hero-arrow{left:806px;top:170px}
.hero-caption{left:131px;top:233px;width:335px;height:81px;background:rgba(30,30,30,.78);padding:14px 0 0 21px;color:#fff}
.hero-caption h1{font-family:'Open Sans',sans-serif;font-weight:400;font-size:13px;letter-spacing:.2px;margin-bottom:7px}
.hero-caption p{font-family:'Open Sans',sans-serif;font-size:8.6px;line-height:17.5px}

.feature{top:372px;width:130px}
.feature h2{font-family:'Open Sans',sans-serif;font-weight:400;font-size:9px;color:#333;margin-bottom:6px;white-space:nowrap}
.feature p{font-size:7.2px;line-height:14px;color:var(--muted)}
.feature-icon{top:371px}

.cta{left:131px;top:462px;width:611px;height:55px;border:1px solid var(--line);background:#fafafa}
.cta p{position:absolute;left:18px;top:12px;width:450px;font-family:'Open Sans',sans-serif;font-style:italic;font-size:8.6px;line-height:16px;color:#555}
.btn{display:block;background:var(--brand);color:#fff;text-align:center;font-family:'Open Sans',sans-serif;font-weight:600;font-size:8.6px;border-radius:2px}
.cta .btn{position:absolute;left:475px;top:14px;width:124px;height:26px;line-height:26px}

.about-title{left:0;top:550px;width:873px;text-align:center;font-family:'Open Sans',sans-serif;font-weight:600;font-size:14.5px;color:var(--brand)}
.about-lead{left:0;top:580px;width:873px;text-align:center;font-size:10px;line-height:19px;color:#222}
.about-body{left:156px;top:624px;width:562px;text-align:center;font-size:7px;line-height:15px;color:var(--muted)}
.about-btn{left:374px;top:682px;width:124px;height:26px;line-height:26px}

.card-media{top:748px;width:192px;height:101px}
.card-title{top:860px;font-family:'Open Sans',sans-serif;font-size:9.5px;color:#333}
.card-text{top:879px;width:192px;font-size:7px;line-height:13.5px;color:var(--muted)}
.overlay-label{left:131px;top:806px;width:192px;text-align:center;font-family:'Open Sans',sans-serif;font-size:7.5px;color:#fff}

.clients{left:0;top:940px;width:873px;height:198px;background:var(--band)}
.clients-title{left:0;top:971px;width:873px;text-align:center;font-family:'Open Sans',sans-serif;font-weight:600;font-size:11.5px;color:var(--brand)}
.avatar{left:161px;top:990px;width:104px;height:104px;border-radius:50%;background:radial-gradient(circle at 50% 40%,#d9dde2,#8c96a3)}
.quote-name{left:0;top:1007px;width:988px;text-align:center;font-family:'Open Sans',sans-serif;font-size:8.6px;color:#222}
.quote-text{left:314px;top:1029px;width:360px;text-align:center;font-size:7.4px;line-height:16px;color:var(--muted)}
.quote-mark{font-family:Georgia,serif;font-size:30px;color:#ccc}

.site-footer{left:0;top:1138px;width:873px;height:62px;background:var(--footer)}
.foot-link{top:1163px;font-size:7.4px;color:#9a9a9a}
.foot-copy{left:542px;top:1163px;width:200px;text-align:right;font-size:6.4px;color:#8a8a8a}
</style>
</head>
<body>

<header class="site-header abs">
  <div class="brand abs"><span class="brand-dot"></span><span class="brand-name">TR Solutions</span></div>
  <nav class="nav">
    <a class="active" href="#">Home</a>
    <a style="left:466px" href="#">About</a>
    <a style="left:537px" href="#">Services</a>
    <a style="left:619px" href="#">Solutions</a>
    <a style="left:705px" href="#">Contact</a>
  </nav>
</header>

<section class="hero abs" role="img" aria-label="Photo of smiling business people meeting in an office"></section>
<svg class="hero-arrow abs" width="18" height="56" viewBox="0 0 18 56"><polyline points="2,2 16,28 2,54" fill="none" stroke="#eee" stroke-width="1"/></svg>
<div class="hero-caption abs">
  <h1>TR SOLUTION IS A PROGRAMMING COMPANY</h1>
  <p>WE SPECIALISE IN BUSINESS FINANCE SOLUTIONS, DESKSUITE<br>AUTOMATION AND PROGRAMMING AND DATA ANALYSIS.</p>
</div>

<svg class="feature-icon abs" style="left:138px" width="30" height="30" viewBox="0 0 30 30">
  <path d="M4 9h7a4 4 0 1 1 7 0h7v7a4 4 0 1 0 0 7v5H4v-6a4 4 0 1 1 0-7z" fill="var(--icon)"/>
</svg>
<div class="feature abs" style="left:182px">
  <h2>BUSINESS FINANCE SOLUTIONS</h2>
  <p>Default model text, and a search for 'lorem ipsum' will uncover many web sites still in their infancy.</p>
</div>

<svg class="feature-icon abs" style="left:358px" width="40" height="30" viewBox="0 0 40 30">
  <circle cx="12" cy="12" r="9" fill="none" stroke="var(--icon)" stroke-width="5" stroke-dasharray="3.5 2.2"/>
  <circle cx="12" cy="12" r="6" fill="var(--icon)"/><circle cx="12" cy="12" r="2.5" fill="#fff"/>
  <circle cx="29" cy="22" r="5" fill="none" stroke="var(--icon)" stroke-width="3" stroke-dasharray="2.5 1.6"/>
  <circle cx="29" cy="22" r="3.5" fill="var(--icon)"/><circle cx="29" cy="22" r="1.3" fill="#fff"/>
</svg>
<div class="feature abs" style="left:406px">
  <h2>DESKSUITE AUTOMATION</h2>
  <p>Default model text, and a search for 'lorem ipsum' will uncover many web sites still in their infancy.</p>
</div>

<svg class="feature-icon abs" style="left:573px" width="32" height="32" viewBox="0 0 32 32">
  <rect x="1" y="1" width="30" height="30" rx="3" fill="var(--icon)"/>
  <rect x="4" y="5" width="24" height="21" fill="#fff"/>
  <path d="M12 9q-3 0-3 3v1.5l-1.5 1.5 1.5 1.5V19q0 3 3 3M20 9q3 0 3 3v1.5l1.5 1.5-1.5 1.5V19q0 3-3 3" fill="none" stroke="var(--icon)" stroke-width="1.5"/>
</svg>
<div class="feature abs" style="left:618px">
  <h2>PROGRAMMING</h2>
  <p>Default model text, and a search for 'lorem ipsum' will uncover many web sites still in their infancy.</p>
</div>

<section class="cta abs">
  <p>Content here, content here', making it look like readable English. Many desktop publishing packages and web page editors now use Lorem Ipsum as their default model text...</p>
  <a class="btn" href="#">GET IN TOUCH</a>
</section>

<h2 class="about-title abs">ABOUT TR SOLUTION</h2>
<p class="about-lead abs">Default model text, and a search for 'lorem ipsum' will uncover many web sites still in their infancy.<br>Various versions have evolved over the years, sometimes by accident.</p>
<p class="about-body abs">Lorem Ipsum is simply dummy text of the printing and typesetting industry. Lorem Ipsum has been the industry's standard dummy text ever since the 1500s, when an unknown printer took a galley of type and scrambled it to make a type specimen book. It has survived not only five centuries, but also the leap into electronic typesetting, remaining essentially unchanged. It was popularised in the 1960s with the release of Typeline sheets containing...</p>
<a class="btn about-btn abs" href="#">READ MORE INFO</a>

<div class="card-media abs" style="left:131px;background:linear-gradient(135deg,#3d6593,#2a4f7d)" role="img" aria-label="Photo of hands typing on a laptop"></div>
<svg class="abs" style="left:220px;top:783px" width="16" height="16" viewBox="0 0 16 16">
  <rect x="1" y="6" width="9" height="5" rx="2.5" transform="rotate(-45 5.5 8.5)" fill="none" stroke="#fff" stroke-width="1.6"/>
  <rect x="6" y="5" width="9" height="5" rx="2.5" transform="rotate(-45 10.5 7.5)" fill="none" stroke="#fff" stroke-width="1.6"/>
</svg>
<div class="overlay-label abs">READ MORE</div>
<div class="card-media abs" style="left:341px;background:linear-gradient(90deg,#e9e6e3,#c9c4c0 50%,#3a3030)" role="img" aria-label="Photo of a businessman with a yes/no dice"></div>
<div class="card-media abs" style="left:550px;background:linear-gradient(180deg,#d7dbe1,#b3bac4)" role="img" aria-label="Illustration of business people climbing steps over a world map"></div>

<div class="card-title abs" style="left:132px">LOREM IPSUM</div>
<p class="card-text abs" style="left:132px">Default model text, and a search for 'lorem ipsum' will uncover many web sites still in their infancy.</p>
<div class="card-title abs" style="left:341px">LOREM IPSUM</div>
<p class="card-text abs" style="left:341px">Default model text, and a search for 'lorem ipsum' will uncover many web sites still in their infancy.</p>
<div class="card-title abs" style="left:551px">LOREM IPSUM</div>
<p class="card-text abs" style="left:551px">Default model text, and a search for 'lorem ipsum' will uncover many web sites still in their infancy.</p>

<section class="clients abs"></section>
<h2 class="clients-title abs">WHAT CLIENTS SAY</h2>
<svg class="abs" style="left:62px;top:1025px" width="12" height="32" viewBox="0 0 12 32"><polyline points="10,1 2,16 10,31" fill="none" stroke="#ccc"/></svg>
<svg class="abs" style="left:792px;top:1025px" width="12" height="32" viewBox="0 0 12 32"><polyline points="2,1 10,16 2,31" fill="none" stroke="#ccc"/></svg>
<div class="avatar abs" role="img" aria-label="Portrait photo of the client"></div>
<div class="quote-mark abs" style="left:284px;top:993px">&ldquo;</div>
<div class="quote-mark abs" style="left:702px;top:1060px">&rdquo;</div>
<div class="quote-name abs">Marcus Hale, Marketing Executive...</div>
<p class="quote-text abs">Content here, content here', making it look like readable English. Many desktop publishing packages and web page editors now use Lorem Ipsum as their default model text, and a search for 'lorem ipsum' will uncover many web sites still in their infancy.</p>

<footer class="site-footer abs"></footer>
<a class="foot-link abs" style="left:133px" href="#">Home</a>
<span class="foot-link abs" style="left:172px">|</span>
<a class="foot-link abs" style="left:193px" href="#">About</a>
<span class="foot-link abs" style="left:231px">|</span>
<a class="foot-link abs" style="left:252px" href="#">Services</a>
<span class="foot-link abs" style="left:299px">|</span>
<a class="foot-link abs" style="left:320px" href="#">Solutions</a>
<span class="foot-link abs" style="left:369px">|</span>
<a class="foot-link abs" style="left:390px" href="#">Contact</a>
<div class="foot-copy abs">Copyrights © TR Solution. All Rights Reserved.</div>

</body>
</html>
```